Header Card Design for Marine Tool Product

We package up our small tools in bags. A nice header card would finish the look.
* Bag is 4" wide. Header Card should be 4x4, folded to 4x2
* Back of card should have 2.25x1.25 area for our part number sticker.
* Design to reinforce the brand and add (perception of) quality to the product.

Brand Website: harbolvex.com

Target Market(s)

Boat Mechanics/Boat owners

Industry/Entity Type

```html
<!DOCTYPE html>
<html lang="en">
<head>
<meta charset="utf-8">
<title>Harbolvex Header Card</title>
<link href="https://fonts.googleapis.com/css2?family=Montserrat:ital,wght@0,400;0,500;0,800;1,800&display=swap" rel="stylesheet">
<style>
  :root {
    --navy: #101a4a;
    --cyan: #4fc6d6;
    --white: #ffffff;
    --page: #ffffff;
    --fold: #e8ecf4;
  }
  * { box-sizing: border-box; margin: 0; padding: 0; }
  html, body { width: 1200px; height: 840px; overflow: hidden; background: var(--page); }
  body { font-family: "Montserrat", Arial, sans-serif; position: relative; }

  .header-card { position: absolute; left: 240px; top: 60px; width: 720px; height: 720px; }
  .panel { position: absolute; left: 0; width: 720px; height: 359px; background: var(--navy); overflow: hidden; }
  .panel--back { top: 0; transform: rotate(180deg); }
  .panel--front { top: 361px; }
  .fold-line { position: absolute; left: 0; top: 359px; width: 720px; height: 2px; background: var(--fold); }

  .hang-hole { position: absolute; left: 274px; width: 174px; height: 70px; }

  .sticker-area { position: absolute; left: 23px; top: 114px; width: 405px; height: 224px; background: var(--white); border-radius: 12px; }

  .back-brand { position: absolute; left: 463px; top: 100px; display: flex; align-items: center; gap: 8px; color: var(--white); font-weight: 800; font-size: 20px; letter-spacing: 0.5px; }
  .back-brand .dot { width: 12px; height: 12px; border-radius: 50%; background: var(--cyan); }

  .contact { position: absolute; left: 463px; top: 182px; color: var(--white); font-weight: 400; font-size: 17px; line-height: 22.8px; }

  .front-brand { position: absolute; left: 0; width: 720px; top: 150px; display: flex; justify-content: center; align-items: center; gap: 12px; color: var(--white); font-weight: 800; font-size: 40px; letter-spacing: 1px; }
  .front-brand .dot { width: 22px; height: 22px; border-radius: 50%; background: var(--cyan); }

  .features { position: absolute; top: 133px; display: flex; flex-direction: column; gap: 12px; }
  .features--left { left: 24px; }
  .features--right { left: 555px; }
  .feature { display: flex; align-items: center; gap: 6px; color: var(--white); font-weight: 800; font-style: italic; font-size: 18px; line-height: 20px; }
  .feature svg { width: 30px; height: 30px; flex: none; }

  .tagline-band { position: absolute; left: 0; bottom: 0; width: 720px; height: 53px; background: var(--cyan); display: flex; align-items: center; justify-content: center; }
  .tagline { color: var(--navy); font-weight: 800; font-style: italic; font-size: 22px; letter-spacing: 0.2px; }
</style>
</head>
<body>
  <div class="header-card">
    <section class="panel panel--back" aria-label="Card back">
      <svg class="hang-hole" style="top:23px" viewBox="0 0 174 70" aria-hidden="true">
        <circle cx="87" cy="28" r="27" fill="var(--white)"/>
        <rect x="0" y="28" width="174" height="42" rx="21" fill="var(--white)"/>
      </svg>
      <div class="sticker-area" aria-label="Part number sticker area"></div>
      <div class="back-brand"><span class="dot"></span>HARBOLVEX</div>
      <address class="contact" style="font-style:normal">
        Company Address<br>
        Here xxxxxxxxxxxxxx<br>
        xxxxxxxxxxxxxxxxxxx<br>
        harbolvex.com<br>
        info@harbolvex.com<br>
        Tel: 01 0000 0000
      </address>
    </section>

    <div class="fold-line"></div>

    <section class="panel panel--front" aria-label="Card front">
      <svg class="hang-hole" style="top:20px" viewBox="0 0 174 70" aria-hidden="true">
        <circle cx="87" cy="28" r="27" fill="var(--white)"/>
        <rect x="0" y="28" width="174" height="42" rx="21" fill="var(--white)"/>
      </svg>

      <div class="front-brand"><span class="dot"></span>HARBOLVEX</div>

      <div class="features features--left">
        <div class="feature">
          <svg viewBox="0 0 30 30" fill="none" stroke="var(--cyan)" stroke-width="2"><path d="M15 6a7 7 0 0 0-4 12.7V22h8v-3.3A7 7 0 0 0 15 6z"/><path d="M12 25h6M15 1v2M4 10l2 1M26 10l-2 1"/></svg>
          <span>Innovative<br>Design</span>
        </div>
        <div class="feature">
          <svg viewBox="0 0 30 30" fill="none" stroke="var(--cyan)" stroke-width="2"><circle cx="15" cy="12" r="8"/><circle cx="15" cy="12" r="4"/><path d="M10 19l-3 9 5-2M20 19l3 9-5-2"/></svg>
          <span>Lifetime<br>Warranty</span>
        </div>
      </div>

      <div class="features features--right">
        <div class="feature">
          <svg viewBox="0 0 30 30" fill="none" stroke="var(--cyan)" stroke-width="2"><path d="M12 18l-4 4a3 3 0 0 1-4-4l4-4M18 12l4-4a3 3 0 0 0-4-4l-4 4M11 19l8-8"/></svg>
          <span>Super<br>Tough</span>
        </div>
        <div class="feature">
          <svg viewBox="0 0 30 30" fill="none" stroke="var(--cyan)" stroke-width="2"><circle cx="15" cy="16" r="11"/><path d="M15 10v6l4 3"/></svg>
          <span>Time<br>Saving</span>
        </div>
      </div>

      <div class="tagline-band">
        <p class="tagline">SPECIALTY TOOLS FOR MARINE MECHANICS</p>
      </div>
    </section>
  </div>
</body>
</html>
```